BFCM Creatives Theme

We are looking for an initial design for our BFCM campaign this year to set the theme for all other creatives for BFCM. We are an ecommerce brand selling Merino wool baby clothing. Our flagship product is the Marlow Toddler Hush Pod (see images).

We are starting with the request for an instagram post, announcing the sale (details below). This post should be 1080x1350 but also look appealing in the square grid. I've attached a basic brand card showing color palette, fonts, and logos. I will also attach some image options. We are looking for your creativity to shine while aligning with our branding and connecting with the customer. If you have a specific idea and are looking for a specific image please contact us.

Sale Details:
- 20% Off Sitewide
- 11.28.24 - 12.02.24
- Excluding giftcards and imperfects. No rainchecks.

```html
<!DOCTYPE html>
<html lang="en">
<head>
<meta charset="utf-8">
<title>fleecewell — 20% Off Sitewide</title>
<link rel="stylesheet" href="https://fonts.googleapis.com/css2?family=Fredoka:wght@400;500;600;700&display=swap">
<style>
  :root {
    --ink: #323537;
    --gold: #c6a64e;
    --slate: #7a8591;
    --paper-light: #f6f5f2;
    --paper-edge: #dfdeda;
    --white: #ffffff;
  }
  html, body {
    margin: 0;
    padding: 0;
    width: 960px;
    height: 1200px;
    overflow: hidden;
  }
  .poster {
    position: relative;
    width: 960px;
    height: 1200px;
    overflow: hidden;
    background: radial-gradient(ellipse 62% 55% at 50% 50%, var(--paper-light) 55%, var(--paper-edge) 100%);
    font-family: "Fredoka", sans-serif;
    color: var(--ink);
  }
  .corner-bands {
    position: absolute;
    inset: 0;
    width: 960px;
    height: 1200px;
  }
  .brand {
    position: absolute;
    left: 99px;
    top: 104px;
    display: flex;
    align-items: center;
    gap: 12px;
  }
  .brand-dot {
    width: 44px;
    height: 44px;
    border-radius: 50%;
    background: var(--white);
    border: 2px solid var(--ink);
    box-sizing: border-box;
  }
  .brand-name {
    font-size: 46px;
    font-weight: 500;
    color: var(--ink);
    line-height: 1;
  }
  .headline {
    position: absolute;
    left: 0;
    right: 0;
    top: 190px;
    margin: 0;
    text-align: center;
    font-size: 232px;
    font-weight: 600;
    line-height: 1;
    letter-spacing: -6px;
    color: var(--ink);
    -webkit-text-stroke: 14px var(--white);
    paint-order: stroke fill;
    filter: drop-shadow(0 0 1px #6c6c6c);
  }
  .subhead {
    position: absolute;
    left: 0;
    right: 0;
    top: 392px;
    margin: 0;
    text-align: center;
    font-size: 146px;
    font-weight: 500;
    line-height: 1;
    letter-spacing: 4px;
    color: var(--gold);
  }
  .product-photo {
    position: absolute;
    width: 169px;
    height: 133px;
    border: 2px solid var(--gold);
    border-radius: 8px;
    box-sizing: border-box;
  }
  .photo-stack   { left: 154px; top: 544px; background: linear-gradient(160deg, #d9cdb8, #b8a993); }
  .photo-blue    { left: 340px; top: 544px; background: linear-gradient(90deg, #eceae7 30%, #7c9fc8 50%, #eceae7 70%); }
  .photo-oat     { left: 523px; top: 544px; background: linear-gradient(180deg, #f1efec, #d8cfc1); }
  .photo-sage    { left: 707px; top: 544px; background: linear-gradient(180deg, #f3f2ef, #b9c7a4); }
  .photo-berry   { left: 118px; top: 693px; background: linear-gradient(90deg, #efe9e3 25%, #efbcc0 50%, #efe9e3 75%); }
  .photo-pink    { left: 303px; top: 693px; background: linear-gradient(90deg, #e4e4e2 30%, #f1c3c4 50%, #e4e4e2 70%); }
  .photo-stripe  { left: 486px; top: 693px; background: linear-gradient(90deg, #e4e4e2 30%, #dfe5d2 50%, #e4e4e2 70%); }
  .photo-cloud   { left: 670px; top: 693px; background: linear-gradient(180deg, #f4f4f2 40%, #8fa9c8 75%, #f4f4f2); }
  .dates {
    position: absolute;
    left: 84px;
    top: 836px;
    margin: 0;
    font-size: 94px;
    font-weight: 500;
    line-height: 1;
    letter-spacing: -1px;
    color: var(--ink);
  }
  .terms-bar {
    position: absolute;
    left: 85px;
    top: 943px;
    width: 706px;
    height: 53px;
    border-radius: 10px;
    background: var(--ink);
    color: var(--white);
    font-size: 37px;
    font-weight: 500;
    line-height: 53px;
    text-align: center;
    margin: 0;
  }
  .terms-note {
    position: absolute;
    left: 85px;
    width: 706px;
    top: 1010px;
    margin: 0;
    text-align: center;
    font-size: 44px;
    font-weight: 500;
    line-height: 1.1;
    color: var(--ink);
  }
</style>
</head>
<body>
  <main class="poster">
    <svg class="corner-bands" viewBox="0 0 960 1200" aria-hidden="true">
      <polygon points="0,0 960,0 960,166 930,166" fill="var(--slate)"/>
      <polygon points="340,0 960,0 960,166 930,166" fill="var(--gold)"/>
      <polygon points="930,1034 960,1034 960,1200 0,1200" fill="var(--slate)"/>
      <polygon points="930,1034 960,1034 960,1200 345,1200" fill="var(--gold)"/>
    </svg>

    <div class="brand">
      <span class="brand-dot"></span>
      <span class="brand-name">fleecewell</span>
    </div>

    <h1 class="headline">20%OFF</h1>
    <h2 class="subhead">SITEWIDE</h2>

    <div class="product-photo photo-stack" role="img" aria-label="Stack of folded printed merino sleep sacks on a wooden stool"></div>
    <div class="product-photo photo-blue" role="img" aria-label="Baby in a blue printed sleep sack lying in a white crib"></div>
    <div class="product-photo photo-oat" role="img" aria-label="Baby sitting on a rug wearing an oatmeal sheep-print sleep sack"></div>
    <div class="product-photo photo-sage" role="img" aria-label="Baby in a sage green sleep sack sitting in a crib"></div>
    <div class="product-photo photo-berry" role="img" aria-label="Pink strawberry-print sleep sack laid flat with accessories"></div>
    <div class="product-photo photo-pink" role="img" aria-label="Baby in a pink strawberry sleep sack lying in a crib"></div>
    <div class="product-photo photo-stripe" role="img" aria-label="Baby in a pale striped sleep sack lying in a crib"></div>
    <div class="product-photo photo-cloud" role="img" aria-label="Baby in a blue cloud-print sleep sack crawling in a crib"></div>

    <p class="dates">11.28.24–12.02.24</p>
    <p class="terms-bar">Excluding giftcards and imperfects.</p>
    <p class="terms-note">No rainchecks.</p>
  </main>
</body>
</html>
```